Tall Fern Roofing Business Card

Need a business card with the logo that was designed here

Contact Information for Business Card

Name, Title, Phone, Email, Website, Company name

```html
<!DOCTYPE html>
<html lang="en">
<head>
<meta charset="utf-8">
<title>Tall Fern Roofing – Business Card</title>
<link href="https://fonts.googleapis.com/css2?family=Open+Sans:wght@400;600;700&family=Montserrat:wght@700&display=swap" rel="stylesheet">
<style>
  :root {
    --backdrop: #262627;
    --card-dark: #202024;
    --brand-blue: #1377c8;
    --blue-deep: #0f66b1;
    --blue-light: #2a8ad6;
    --silver: #a9abae;
    --white: #ffffff;
    --corner: 120px;
  }
  * { box-sizing: border-box; margin: 0; padding: 0; }
  html, body {
    width: 1200px; height: 780px; overflow: hidden;
    background: var(--backdrop);
    font-family: "Open Sans", Arial, sans-serif;
  }
  .canvas {
    width: 1200px; height: 780px;
    display: flex; align-items: center; justify-content: center; gap: 80px;
  }
  .card {
    width: 380px; height: 640px; position: relative; overflow: hidden;
  }
  /* Front side */
  .card--front {
    border-radius: var(--corner) 0 var(--corner) 0;
    background: var(--brand-blue);
    display: flex; align-items: center; justify-content: center;
  }
  .front-pattern {
    position: absolute; inset: 0;
    background: linear-gradient(160deg, var(--blue-light) 0%, var(--brand-blue) 45%, var(--blue-deep) 100%);
  }
  .front-brand {
    position: relative;
    display: flex; align-items: center; gap: 12px;
    font-weight: 700; font-size: 30px; color: var(--white);
  }
  .brand-square {
    width: 18px; height: 18px; background: var(--white);
  }
  /* Back side */
  .card--back {
    border-radius: 0 var(--corner) 0 var(--corner);
    background: var(--card-dark);
    padding: 44px 40px 56px 40px;
    display: flex; flex-direction: column; justify-content: space-between;
  }
  .back-brand {
    display: flex; align-items: center; gap: 10px;
    font-weight: 700; font-size: 24px; color: var(--silver);
  }
  .back-brand .brand-square { background: var(--brand-blue); width: 14px; height: 14px; }
  .details { align-self: flex-end; color: var(--white); width: 270px; }
  .person-name {
    font-family: "Montserrat", Arial, sans-serif; font-weight: 700;
    font-size: 34px; line-height: 1.05; letter-spacing: 0.5px;
  }
  .person-name .first { color: var(--brand-blue); }
  .person-name .last { color: var(--silver); }
  .person-title { font-weight: 600; font-size: 15px; margin: 4px 0 22px 70px; }
  .address { font-size: 14px; line-height: 1.45; margin-bottom: 20px; }
  .contact-list { list-style: none; font-size: 14px; line-height: 1.5; }
  .contact-list li { display: flex; align-items: center; gap: 10px; }
  .contact-list svg { width: 14px; height: 14px; flex: none; fill: var(--brand-blue); }
</style>
</head>
<body>
<main class="canvas">
  <section class="card card--front" aria-label="Card front">
    <div class="front-pattern" role="img" aria-label="Repeating pattern of small house roof outlines in tonal blues"></div>
    <div class="front-brand"><span class="brand-square"></span>Tall Fern Roofing</div>
  </section>

  <section class="card card--back" aria-label="Card back">
    <div class="back-brand"><span class="brand-square"></span>Tall Fern Roofing</div>
    <div class="details">
      <h1 class="person-name"><span class="first">Dale</span> <span class="last">Mercer</span></h1>
      <p class="person-title">Co-Founder</p>
      <p class="address">1840 Ridgeline Ave. Suite 300<br>Cedar Falls, TX 75410</p>
      <ul class="contact-list">
        <li><svg viewBox="0 0 24 24" aria-hidden="true"><path d="M6.6 10.8a15.1 15.1 0 0 0 6.6 6.6l2.2-2.2a1 1 0 0 1 1-.25 11.4 11.4 0 0 0 3.6.57 1 1 0 0 1 1 1V20a1 1 0 0 1-1 1A17 17 0 0 1 3 4a1 1 0 0 1 1-1h3.5a1 1 0 0 1 1 1c0 1.25.2 2.45.57 3.57a1 1 0 0 1-.25 1z"/></svg>(555) 204-6731</li>
        <li><svg viewBox="0 0 24 24" aria-hidden="true"><path d="M12 2a10 10 0 1 0 0 20 10 10 0 0 0 0-20zm6.9 6h-2.9a15.6 15.6 0 0 0-1.4-3.6A8 8 0 0 1 18.9 8zM12 4c.8 1.2 1.5 2.5 1.9 4h-3.8c.4-1.5 1.1-2.8 1.9-4zM4.3 14a8 8 0 0 1 0-4h3.4a16.5 16.5 0 0 0 0 4zm.8 2h2.9c.3 1.3.8 2.5 1.4 3.6A8 8 0 0 1 5.1 16zM8 8H5.1a8 8 0 0 1 4.3-3.6C8.8 5.5 8.3 6.7 8 8zm4 12c-.8-1.2-1.5-2.5-1.9-4h3.8c-.4 1.5-1.1 2.8-1.9 4zm2.3-6H9.7a14.7 14.7 0 0 1 0-4h4.6a14.7 14.7 0 0 1 0 4zm.3 5.6c.6-1.1 1.1-2.3 1.4-3.6h2.9a8 8 0 0 1-4.3 3.6zm1.7-5.6a16.5 16.5 0 0 0 0-4h3.4a8 8 0 0 1 0 4z"/></svg>info@tallfernroofing.com</li>
        <li><svg viewBox="0 0 24 24" aria-hidden="true"><path d="M3 5h18a1 1 0 0 1 1 1v12a1 1 0 0 1-1 1H3a1 1 0 0 1-1-1V6a1 1 0 0 1 1-1zm1 2.4V17h16V7.4l-8 5.3z M5 7l7 4.6L19 7z"/></svg>www.tallfernroofing.com</li>
      </ul>
    </div>
  </section>
</main>
</body>
</html>
```